Corvel Capital LLC

Need Professional Business cards for New Investment Fund

Target Market(s)

High Quality investors

Industry/Entity Type

Financial

Contact Information for Business Card

Phone Number +1 555 284 6190
Name Lukas Varenko
Title Fund Manager
email lv@FundCorvel.com
Website www.FundCorvel.com

Colors

Designer to choose colors to be used in the design.

Requirements
Must have
• Must have our Logo and all of the above. Must be made so lettering and loge can be raised

```html
<!DOCTYPE html>
<html lang="en">
<head>
<meta charset="utf-8">
<title>Corvel Capital LLC — Business Card</title>
<link rel="stylesheet" href="https://fonts.googleapis.com/css2?family=Oswald:wght@600&family=Poppins:wght@300;400&display=swap">
<style>
  :root {
    --backdrop: #6f6f6f;
    --paper: #f4f4f2;
    --forest: #34412f;
    --neon: #22e30f;
    --slate: #4c5a4c;
    --ink: #3a3a3a;
    --mist: #e9e9e7;
  }
  * { box-sizing: border-box; margin: 0; padding: 0; }
  html, body { width: 1200px; height: 1074px; overflow: hidden; }
  body {
    background: var(--backdrop);
    font-family: "Poppins", sans-serif;
    position: relative;
  }
  .card {
    position: absolute;
    left: 250px;
    width: 700px;
    height: 400px;
    border-bottom: 4px solid var(--neon);
    border-radius: 3px;
    box-shadow: 0 18px 40px rgba(0,0,0,.35);
  }
  .card--front { top: 90px; background: var(--paper); }
  .card--back  { top: 570px; background: var(--forest); }

  .brand {
    display: flex;
    align-items: center;
    gap: 14px;
    font-family: "Oswald", sans-serif;
    font-weight: 600;
    letter-spacing: 2px;
    text-transform: uppercase;
  }
  .brand__mark { width: 26px; height: 26px; background: var(--neon); }
  .card--front .brand {
    position: absolute; left: 60px; top: 60px;
    font-size: 34px; color: var(--slate);
  }
  .card--back .brand {
    position: absolute; left: 50%; top: 50%;
    transform: translate(-50%, -50%);
    font-size: 46px; color: var(--mist);
  }
  .card--back .brand__mark { width: 34px; height: 34px; }

  .contact {
    position: absolute;
    right: 60px;
    bottom: 50px;
    width: 300px;
  }
  .contact__name {
    font-family: "Oswald", sans-serif;
    font-weight: 600;
    font-size: 30px;
    color: var(--neon);
    text-transform: uppercase;
    letter-spacing: .5px;
    line-height: 1.1;
  }
  .contact__title {
    font-size: 17px;
    font-weight: 400;
    color: var(--ink);
    margin-bottom: 18px;
  }
  .contact__list { list-style: none; }
  .contact__item {
    display: flex;
    align-items: center;
    gap: 10px;
    font-size: 16px;
    font-weight: 300;
    color: var(--ink);
    line-height: 1.7;
  }
  .contact__icon { width: 13px; height: 13px; flex: none; }
</style>
</head>
<body>
  <section class="card card--front" aria-label="Business card front">
    <div class="brand"><span class="brand__mark"></span>Corvel Capital</div>
    <div class="contact">
      <p class="contact__name">Lukas Varenko</p>
      <p class="contact__title">Fund Manager</p>
      <ul class="contact__list">
        <li class="contact__item">
          <svg class="contact__icon" viewBox="0 0 24 24" aria-hidden="true"><path fill="#22e30f" d="M6.6 10.8a15 15 0 0 0 6.6 6.6l2.2-2.2a1 1 0 0 1 1-.25 11.4 11.4 0 0 0 3.6.57 1 1 0 0 1 1 1V20a1 1 0 0 1-1 1A17 17 0 0 1 3 4a1 1 0 0 1 1-1h3.5a1 1 0 0 1 1 1c0 1.25.2 2.45.57 3.57a1 1 0 0 1-.25 1z"/></svg>
          +1 555 284 6190
        </li>
        <li class="contact__item">
          <svg class="contact__icon" viewBox="0 0 24 24" aria-hidden="true"><rect x="2" y="5" width="20" height="14" rx="1" fill="#22e30f"/><path d="M3 6l9 7 9-7" fill="none" stroke="#f4f4f2" stroke-width="2"/></svg>
          lv@FundCorvel.com
        </li>
        <li class="contact__item">
          <svg class="contact__icon" viewBox="0 0 24 24" aria-hidden="true"><circle cx="12" cy="12" r="10" fill="#22e30f"/><path d="M2 12h20M12 2c3 3 3 17 0 20M12 2c-3 3-3 17 0 20" fill="none" stroke="#f4f4f2" stroke-width="1.6"/></svg>
          www.FundCorvel.com
        </li>
      </ul>
    </div>
  </section>

  <section class="card card--back" aria-label="Business card back">
    <div class="brand"><span class="brand__mark"></span>Corvel Capital</div>
  </section>
</body>
</html>
```